Lorvex Tilo medical cannibis cultivation company

tag - Tilo rise
Lorvex Tilo medical cannabis cultivation - logo is selected- can we please see bold examples with our selection. We are mainly dealing with medical companies and professionals. We would like to be stand out in the crowd with our designs. Welcome any and all attempts. Thanks

Target Market(s)

Medical and Professional

Industry/Entity Type

Medical And Science

Font styles to use
Sans Serif

Colors

Designer to choose colors to be used in the design.

Requirements
Must have
• Bright colour and be bold- Love the teal and magenta that is currently on the dark background design.
Nice to have
• shading and the 3D affect- The shadowed appearance.
Should not have
• Anything related to illegal activity or un professional manners

```html
<!DOCTYPE html>
<html lang="en">
<head>
<meta charset="utf-8">
<title>Lorvex Tilo – Business Card</title>
<link rel="stylesheet" href="https://fonts.googleapis.com/css2?family=Cinzel:wght@400;600&family=Libre+Baskerville&display=swap">
<style>
  :root {
    --bg: #e6e1d8;
    --magenta: #9c4a9a;
    --teal: #00aee8;
    --ink: #0a0a0a;
    --grey: #9a9ca3;
    --light: #d9d9de;
  }
  html, body {
    margin: 0;
    padding: 0;
    overflow: hidden;
  }
  .canvas {
    position: relative;
    width: 1200px;
    height: 1040px;
    background: var(--bg);
    overflow: hidden;
  }
  .card {
    position: absolute;
    left: 220px;
    width: 760px;
    height: 434px;
    border-radius: 26px;
    overflow: hidden;
    box-shadow: 0 14px 28px rgba(0,0,0,0.28), 0 3px 6px rgba(0,0,0,0.2);
  }
  .card--front { top: 60px; background: var(--magenta); }
  .card--back { top: 546px; background: var(--ink); }

  .front-shape {
    position: absolute;
    inset: 0;
  }
  .holder {
    position: absolute;
    left: 44px;
    top: 40px;
    font-family: "Cinzel", serif;
    color: var(--ink);
    white-space: nowrap;
  }
  .holder__name {
    font-size: 34px;
    font-weight: 400;
    letter-spacing: 1px;
    line-height: 1;
  }
  .holder__role {
    font-size: 21px;
    margin-top: 8px;
    letter-spacing: 0.5px;
  }
  .contact {
    position: absolute;
    right: 22px;
    top: 180px;
    font-family: "Libre Baskerville", serif;
    font-size: 15px;
    color: var(--ink);
    text-align: right;
    line-height: 22px;
    white-space: nowrap;
  }
  .contact__row {
    display: flex;
    justify-content: flex-end;
    align-items: center;
    gap: 12px;
  }
  .contact__row--gap { margin-top: 10px; }
  .contact__icon {
    width: 15px;
    height: 15px;
    flex: none;
  }
  .contact__icon--blank { visibility: hidden; }

  .brand {
    position: absolute;
    left: 50%;
    top: 50%;
    transform: translate(-50%, -50%);
    display: flex;
    align-items: center;
    gap: 22px;
    white-space: nowrap;
  }
  .brand__text { text-align: left; }
  .brand__name {
    font-family: "Cinzel", serif;
    font-weight: 600;
    font-size: 46px;
    color: var(--teal);
    letter-spacing: 1px;
    line-height: 1;
  }
  .brand__tag {
    display: flex;
    align-items: center;
    gap: 10px;
    margin-top: 10px;
    font-family: "Cinzel", serif;
    font-size: 17px;
    letter-spacing: 4px;
    color: var(--light);
  }
  .brand__rule {
    height: 1px;
    width: 40px;
    background: var(--light);
  }
  .brand__ring {
    flex: none;
    width: 118px;
    height: 118px;
    border-radius: 50%;
    border: 4px solid var(--grey);
    box-sizing: border-box;
  }
</style>
</head>
<body>
<div class="canvas">

  <section class="card card--front">
    <svg class="front-shape" viewBox="0 0 760 434" width="760" height="434" aria-hidden="true">
      <path fill="var(--ink)" transform="translate(-6 -14)" d="M0 180 C70 205 140 240 185 272 C225 215 260 195 309 176 C400 140 460 100 534 93 C620 86 700 95 770 110 L770 450 L0 450 Z"/>
      <path fill="var(--teal)" d="M0 180 C70 205 140 240 185 272 C225 215 260 195 309 176 C400 140 460 100 534 93 C620 86 700 95 760 110 L760 434 L0 434 Z"/>
      <circle cx="188" cy="204" r="11" fill="var(--ink)"/>
    </svg>

    <div class="holder">
      <div class="holder__name">Maren Holt</div>
      <div class="holder__role">CEO/Founder</div>
    </div>

    <div class="contact">
      <div class="contact__row"><span>4120 Alder Row</span>
        <svg class="contact__icon contact__icon--blank" viewBox="0 0 16 16"></svg></div>
      <div class="contact__row"><span>Kestrel Bay, Norland 20816</span>
        <svg class="contact__icon contact__icon--blank" viewBox="0 0 16 16"></svg></div>

      <div class="contact__row contact__row--gap"><span>555 210 4471</span>
        <svg class="contact__icon" viewBox="0 0 16 16" aria-hidden="true"><path fill="var(--ink)" d="M3 1 L6 1 L7 5 L5 6.5 C6 9 7 10 9.5 11 L11 9 L15 10 L15 13 C15 14 14 15 13 15 C7 15 1 9 1 3 C1 2 2 1 3 1 Z"/></svg></div>
      <div class="contact__row"><span>555 382 9065</span>
        <svg class="contact__icon" viewBox="0 0 16 16" aria-hidden="true"><rect x="4" y="1" width="8" height="14" rx="1.5" fill="none" stroke="var(--ink)" stroke-width="1.6"/></svg></div>
      <div class="contact__row"><span>555 764 1302</span>
        <svg class="contact__icon" viewBox="0 0 16 16" aria-hidden="true"><rect x="1" y="5" width="14" height="9" rx="1" fill="var(--ink)"/><rect x="4" y="1" width="8" height="4" fill="var(--ink)"/></svg></div>
      <div class="contact__row"><span>maren@lorvextilo.com</span>
        <svg class="contact__icon" viewBox="0 0 16 16" aria-hidden="true"><rect x="1" y="3" width="14" height="10" fill="var(--ink)"/><path d="M1 3 L8 9 L15 3" fill="none" stroke="var(--teal)" stroke-width="1.4"/></svg></div>
      <div class="contact__row"><span>www.lorvextilo.com</span>
        <svg class="contact__icon" viewBox="0 0 16 16" aria-hidden="true"><circle cx="8" cy="8" r="7" fill="var(--ink)"/><path d="M1 8 H15 M8 1 C5 4 5 12 8 15 M8 1 C11 4 11 12 8 15" fill="none" stroke="var(--teal)" stroke-width="1"/></svg></div>
    </div>
  </section>

  <section class="card card--back">
    <div class="brand">
      <div class="brand__text">
        <div class="brand__name">Lorvex Tilo</div>
        <div class="brand__tag"><span class="brand__rule"></span>Tilo rise<span class="brand__rule"></span></div>
      </div>
      <div class="brand__ring"></div>
    </div>
  </section>

</div>
</body>
</html>
```